Product label for herbal salves, lotions, soaps and tinctures

We need a very simple, clean and organic looking label that can be used for an ointment jar, a lotion bottle and a dropper bottle.
We have an existing logo (see attached). We like the colors white, olive green, gold and black. It needs to include product name as dominant and logo. It also needs to include an ingredient list, and usage statement. Include weight of product, distributed by, made in the USA, and QVX statement.
Example of what needs to be present:
Logo
Name: Tranquil Ease Blend
Used for: For Muscle Aches, Arthritis, Tendonitis, Headaches
To Use: For muscle aches, arthritis and tendonitis, massage into affected area. For tension headache apply to neck, temples and forehead.
Store in a cool and dry place, away from direct heat and sunlight.
Weight of product: 1.75
DIST. BY: Copper Brook Herbal
Made in the USA
This product is not intended to diagnose, treat, cure
or prevent any disease. Not regulated
by the QVX. Please consult your health care practitioner
before using product. Discontinue use if any adverse reaction occurs.
Ingredient list:
Wildcrafted Ingredients:
Ashwagandha Root, Peppermint Leaf, Hops Flowers, St. John’s Wort Herb, Arnica Flowers, Green Tea Leaf, Alfalfa Leaf, Dandelion Root, Burdock Root, Chickweed Herb, Chaparral Leaf, Yarrow Flowers, Boneset Herb, Moringa Leaf, Meadowsweet Herb, Nettle Leaf
Organic Ingredients:
Olive Oil, Aloe Leaf, Sweet Birch Bark, Helichrysum Flowers, Holy Basil Leaf, Borage Herb, Ginger Root, Angelica Root, White Willow Bark, Mustard Seed, Beeswax, Vitamin E, Essential Oils
Dimensions of Jar:
Circumference: 7 in.
Height: 1 in.

```html
<!DOCTYPE html>
<html lang="en">
<head>
<meta charset="utf-8">
<title>Tranquil Ease Blend – Copper Brook Herbal</title>
<link href="https://fonts.googleapis.com/css2?family=Barlow:ital,wght@0,400;0,600;0,700;1,600;1,700&family=Playfair+Display:wght@500&display=swap" rel="stylesheet">
<style>
  :root {
    --olive: #5a7417;
    --olive-soft: #e6e9d8;
    --ink: #111111;
    --paper: #ffffff;
    --gold-dark: #8a5a1e;
    --gold-mid: #d9a93c;
    --gold-light: #f3ec74;
    --dieline: #e0201b;
  }
  * { box-sizing: border-box; margin: 0; padding: 0; }
  html, body { width: 1200px; height: 560px; overflow: hidden; background: var(--paper); }
  .label {
    position: relative;
    width: 1200px;
    height: 560px;
    background: var(--paper);
    border: 1.5px solid var(--dieline);
    border-radius: 22px;
    overflow: hidden;
    font-family: "Barlow", sans-serif;
    color: var(--ink);
  }
  .gold-band {
    position: absolute;
    left: 0; right: 0;
    height: 12px;
    background: linear-gradient(90deg, var(--gold-dark) 0%, var(--gold-mid) 25%, var(--gold-light) 50%, var(--gold-mid) 75%, var(--gold-dark) 100%);
  }
  .gold-band--top { top: 0; }
  .gold-band--bottom { bottom: 0; }

  /* Front panel */
  .brand {
    position: absolute;
    left: 160px; top: 110px;
    width: 310px;
    display: flex;
    align-items: center;
    justify-content: center;
    gap: 10px;
  }
  .brand__dot { width: 16px; height: 16px; border-radius: 50%; background: var(--olive); flex: none; }
  .brand__name { font-weight: 700; font-size: 28px; color: var(--olive); letter-spacing: 0.3px; white-space: nowrap; }

  .product-name {
    position: absolute;
    left: 120px; top: 252px;
    width: 400px;
    text-align: center;
    font-family: "Playfair Display", serif;
    font-weight: 500;
    font-size: 33px;
    line-height: 41px;
    text-transform: uppercase;
  }
  .uses {
    position: absolute;
    left: 253px; top: 385px;
    border-left: 2px solid var(--ink);
    padding-left: 18px;
    list-style: none;
    font-size: 19.5px;
    line-height: 23.6px;
  }
  .net-weight { position: absolute; left: 274px; top: 500px; font-weight: 600; font-size: 16px; }

  /* Back panel */
  .info {
    position: absolute;
    left: 741px; top: 34px;
    width: 355px;
    font-size: 15.3px;
    line-height: 15.7px;
    text-align: justify;
  }
  .info p { margin-bottom: 15.7px; }
  .info__heading { font-weight: 600; margin-bottom: 0 !important; }
  .info__group { font-weight: 700; font-style: italic; color: var(--olive); }
  .info__ingredients { margin-bottom: 0 !important; }
  .info__ingredients + .info__group { display: block; }
  .info__lead { font-weight: 600; color: var(--olive); }
  .info p.info__ingredients--last { margin-bottom: 15.7px !important; }

  .origin {
    position: absolute;
    left: 880px; top: 468px;
    width: 160px;
    text-align: center;
    font-weight: 700; font-style: italic;
    font-size: 15px;
    color: var(--olive);
  }
  .distributor { position: absolute; left: 870px; top: 499px; font-weight: 700; font-size: 13.5px; }
  .distributor-dot {
    position: absolute;
    left: 800px; top: 490px;
    width: 22px; height: 22px;
    border-radius: 50%;
    background: var(--olive);
  }
</style>
</head>
<body>
<div class="label">
  <div class="gold-band gold-band--top"></div>

  <div class="brand">
    <span class="brand__dot"></span>
    <span class="brand__name">Copper Brook Herbal</span>
  </div>

  <h1 class="product-name">Tranquil Ease<br>Blend</h1>

  <ul class="uses">
    <li>Muscle Aches</li>
    <li>Arthritis</li>
    <li>Tendonitis</li>
    <li>Headaches</li>
  </ul>

  <div class="net-weight">1.75 OZ</div>

  <div class="info">
    <p class="info__heading">INGREDIENT LIST:</p>
    <span class="info__group">Wildcrafted Ingredients:</span>
    <p class="info__ingredients">Ashwagandha Root, Peppermint Leaf, Hops Flowers, St. John’s Wort Herb, Arnica Flowers, Green Tea Leaf, Alfalfa Leaf, Dandelion Root, Burdock Root, Chickweed Herb, Chaparral Leaf, Yarrow Flowers, Boneset Herb, Moringa Leaf, Meadowsweet Herb, Nettle Leaf.</p>
    <span class="info__group">Organic Ingredients:</span>
    <p class="info__ingredients info__ingredients--last">Olive Oil, Aloe Leaf, Sweet Birch Bark, Helichrysum Flowers, Holy Basil Leaf, Borage Herb, Ginger Root, Angelica Root, White Willow Bark, Mustard Seed, Beeswax, Vitamin E, Essential Oils.</p>
    <p><span class="info__lead">TO USE:</span> For muscle aches, arthritis and tendonitis, massage into affected area. For tension headache apply to neck, temples and forehead.</p>
    <p>Store in a cool and dry place, away from direct heat and sunlight.</p>
    <p>This product is not intended to diagnose, treat, cure or prevent any disease. Not regulated by the QVX. Please consult your health care practitioner before using product. Discontinue use if any adverse reaction occurs.</p>
  </div>

  <span class="distributor-dot"></span>
  <div class="origin">- Made in the USA -</div>
  <div class="distributor">DIST. BY: COPPER BROOK HERBAL</div>

  <div class="gold-band gold-band--bottom"></div>
</div>
</body>
</html>
```